independent Business Card Design

I am an independent consultant predominantly with non-profit groups but also start-ups. I manage marketing projects that relate to major campaigns for fund-raising and community awareness. I also have a linked in address... https://www.linkedin.com/profile/public-profile-settings?trk=prof-edit-edit-public_profileI am looking for a simple/clean card do distribute at a symposium I am attending next week!

Target Market(s)

Harbor-Row C-Execs

Industry/Entity Type

Non-Profit

Contact Information for Business Card

Nora J Pelvane
555-214-0376
pelvanenj@mailvora.example

```html
<!DOCTYPE html>
<html lang="en">
<head>
<meta charset="utf-8">
<title>Nora J Pelvane – Business Card</title>
<link rel="stylesheet" href="https://fonts.googleapis.com/css2?family=Dancing+Script:wght@500&family=Montserrat:wght@400&display=swap">
<style>
  :root {
    --page-bg: #e9e7e3;
    --frame: #5e5e5e;
    --frame-line: #f4f1ec;
    --card-face: #f2efea;
    --ink: #5a5a5a;
    --ink-soft: #6e6e6e;
  }
  * { margin: 0; padding: 0; box-sizing: border-box; }
  html, body {
    width: 1200px;
    height: 800px;
    overflow: hidden;
    background: var(--page-bg);
  }
  .canvas {
    position: relative;
    width: 1200px;
    height: 800px;
    display: flex;
    align-items: center;
    justify-content: center;
  }
  .business-card {
    position: relative;
    width: 900px;
    height: 514px;
    background: var(--frame);
    padding: 26px;
    box-shadow: 0 6px 18px rgba(0,0,0,0.18);
  }
  .card-rule {
    width: 100%;
    height: 100%;
    border: 5px solid var(--frame-line);
    padding: 4px;
    background: var(--frame-line);
  }
  .card-face {
    position: relative;
    width: 100%;
    height: 100%;
    background: var(--card-face);
    outline: 2px solid var(--frame);
  }
  .holder-name {
    position: absolute;
    top: 112px;
    left: 0;
    right: 0;
    text-align: center;
    font-family: "Dancing Script", cursive;
    font-weight: 500;
    font-size: 92px;
    color: var(--ink);
    letter-spacing: 1px;
  }
  .holder-role {
    position: absolute;
    top: 240px;
    left: 0;
    right: 0;
    text-align: center;
    font-family: "Montserrat", sans-serif;
    font-size: 21px;
    color: var(--ink-soft);
    letter-spacing: 0.5px;
  }
  .contact {
    position: absolute;
    display: flex;
    align-items: center;
    gap: 12px;
    font-family: "Montserrat", sans-serif;
    font-size: 21px;
    color: var(--ink-soft);
  }
  .contact-icon { width: 28px; height: 28px; flex: none; }
  .contact--email { right: 34px; top: 318px; }
  .contact--phone { left: 34px; bottom: 26px; }
</style>
</head>
<body>
<main class="canvas">
  <article class="business-card">
    <div class="card-rule">
      <div class="card-face">
        <h1 class="holder-name">Nora J Pelvane</h1>
        <p class="holder-role">Marketing Management</p>

        <p class="contact contact--email">
          <svg class="contact-icon" viewBox="0 0 28 28" aria-hidden="true">
            <rect width="28" height="28" fill="var(--ink)"/>
            <rect x="5" y="8" width="18" height="12" fill="none" stroke="var(--card-face)" stroke-width="1.6"/>
            <polyline points="5,8 14,15 23,8" fill="none" stroke="var(--card-face)" stroke-width="1.6"/>
          </svg>
          <span>pelvanenj@mailvora.example</span>
        </p>

        <p class="contact contact--phone">
          <svg class="contact-icon" viewBox="0 0 28 28" aria-hidden="true">
            <rect width="28" height="28" fill="var(--ink)"/>
            <rect x="9" y="4" width="10" height="20" rx="1.5" fill="none" stroke="var(--card-face)" stroke-width="1.6"/>
            <rect x="11" y="7" width="6" height="6" fill="var(--card-face)"/>
            <circle cx="14" cy="19.5" r="1.4" fill="var(--card-face)"/>
          </svg>
          <span>555-214-0376</span>
        </p>
      </div>
    </div>
  </article>
</main>
</body>
</html>
```